Wordpress Website - for cutting edge Artificial Intelligence company

We need a wordpress web site for our company Varlomex.

Objective:
- To promote our software products to potential customers (e.g. large corporations)
- To promote our software products to potential partners (e.g. software makers who want to bundle our software inside their products)
- To promote our company to potential Investors (venture capital funds, angel investors, etc.)

Sample content and proposed structure can be found in the attached file.
Company logo is also attached.

The Plover logo should only be used in the section relating to the Plover Product (e.g. Plover Text & Plover Speech)

Target Market(s)

Core Target Market:
- Large corporations (e.g. Major Banks, Retailers & Pharmaceutical companies) who could buy our software

Industry/Entity Type

Software

Coding

Coded - Design and coding required

Font styles to use
Sans Serif

Colors
ffffff
ec1f27
000000
757575
dfdfdf
9bcb3c

Requirements
Must have
• Functionality:
• - Designed in Wordpress (using tools from wordpress.org, not hosted on wordpress.com)
• - Must have a user friendly CMS module for us to make updates easily
• - Must be designed to look great across different devices
• - Must be designed to look great in English and Chinese (as well as other future languages).

```html
<!DOCTYPE html>
<html lang="en">
<head>
<meta charset="utf-8">
<title>Varlomex – Artificial Intelligence</title>
<link rel="stylesheet" href="https://fonts.googleapis.com/css2?family=Open+Sans:wght@400;600;700&display=swap">
<style>
:root{
  --white:#ffffff;
  --red:#ec1f27;
  --black:#000000;
  --grey:#757575;
  --light:#dfdfdf;
  --green:#9bcb3c;
  --section:#f2f2f2;
  --footer:#1d1d1f;
  --footer-bar:#111112;
  --hero-deep:#07152e;
  --hero-mid:#1d3e6a;
}
*{box-sizing:border-box;margin:0;padding:0}
html,body{width:1200px;height:2448px;overflow:hidden}
body{font-family:"Open Sans",Arial,sans-serif;color:var(--black);background:var(--white);position:relative}

/* Header */
.site-header{height:68px;display:flex;align-items:center;justify-content:space-between;padding:0 140px 0 140px;background:var(--white)}
.brand{font-size:26px;font-weight:700;color:var(--red);letter-spacing:1px}
.main-nav{display:flex;align-items:center;gap:18px;font-size:11px;font-weight:600;color:var(--black);text-transform:uppercase}
.main-nav .active{border-bottom:2px solid var(--red);padding-bottom:4px;padding-top:6px}
.lang-btn{background:var(--red);color:var(--white);padding:4px 10px;font-size:10px;margin-left:8px}

/* Hero */
.hero{position:relative;height:596px;background:radial-gradient(ellipse at 25% 45%,#3b6fa8 0%,var(--hero-mid) 30%,var(--hero-deep) 75%);text-align:center;color:var(--white)}
.hero-visual{position:absolute;inset:0}
.hero-copy{position:absolute;top:258px;left:0;right:0}
.hero-title{font-size:30px;font-weight:400}
.hero-title span{color:var(--red)}
.hero-sub{font-size:17px;margin-top:8px}
.btn-more{display:inline-block;margin-top:34px;background:#7d7d7d;color:var(--white);font-size:11px;font-weight:600;padding:10px 36px;text-transform:uppercase}
.hero-arrow{position:absolute;top:350px}
.hero-arrow.left{left:24px}
.hero-arrow.right{right:24px}
.cta-row{position:absolute;bottom:0;left:356px;display:flex}
.cta{width:244px;height:58px;display:flex;align-items:center;justify-content:center;gap:10px;font-size:12px;font-weight:700;color:var(--white);text-transform:uppercase}
.cta.demo{background:var(--red)}
.cta.contact{background:var(--green)}

/* News */
.news{padding-top:50px;height:956px}
.section-title{text-align:center;font-size:28px;font-weight:400;color:#333}
.title-rule{width:360px;height:1px;background:var(--light);margin:18px auto 0}
.news-grid{display:grid;grid-template-columns:repeat(3,290px);gap:32px 24px;justify-content:center;margin-top:32px}
.news-card{height:328px;background:var(--black)}
.news-image{height:232px}
.news-body{padding:14px 14px;color:var(--white);font-size:11px;line-height:1.5}
.news-meta{font-size:10px;font-weight:700;margin-bottom:6px}
.news-meta span{color:var(--red)}
.img-a{background:linear-gradient(135deg,#e8ecef,#9aa6b0)}
.img-b{background:linear-gradient(135deg,#5d7894,#1e3148)}
.img-c{background:linear-gradient(135deg,#0a2a5a,#2d7dc8)}
.img-d{background:linear-gradient(135deg,#cfc6b8,#6f6a62)}
.img-e{background:linear-gradient(135deg,#aab8c8,#4c6178)}
.img-f{background:linear-gradient(135deg,#d7dde3,#5d6a78)}
.pager{display:flex;justify-content:center;gap:18px;margin-top:38px}

/* Testimonials */
.stories{height:520px;background:var(--section);padding-top:56px}
.stories .title-rule{background:#cfcfcf}
.story-row{display:grid;grid-template-columns:repeat(3,300px);gap:50px;justify-content:center;margin-top:36px;text-align:center}
.avatar{width:132px;height:132px;border-radius:50%;margin:0 auto;background:radial-gradient(circle at 50% 40%,#c9b8a6,#5a5d66);border:4px solid var(--white)}
.story-name{margin-top:22px;font-size:11px;font-weight:700;color:var(--red)}
.story-name span{color:var(--grey);font-weight:400}
.story-text{margin-top:10px;font-size:11px;line-height:1.6;color:var(--grey)}

/* Footer */
.site-footer{height:308px;background:var(--footer);position:relative;color:#bdbdbd}
.footer-main{display:flex;padding:58px 140px 0 140px}
.footer-brand{width:220px;font-size:22px;font-weight:700;color:var(--white);letter-spacing:1px}
.footer-col{width:180px;font-size:11px;line-height:2}
.footer-col h4{color:var(--red);font-size:11px;font-weight:600;margin-bottom:8px}
.footer-bar{position:absolute;bottom:0;left:0;right:0;height:48px;background:var(--footer-bar);display:flex;align-items:center;justify-content:space-between;padding:0 24px;font-size:10px;color:#9a9a9a}
.footer-bar .legal{display:flex;align-items:center;gap:10px}
</style>
</head>
<body>

<header class="site-header">
  <div class="brand">VARLOMEX</div>
  <nav class="main-nav">
    <span class="active">Artificial Intelligence</span>
    <span>Products</span>
    <span>Services</span>
    <span>Partners</span>
    <span>Contact Us</span>
    <span>About Us</span>
    <span class="lang-btn">中文</span>
    <span>Login</span>
  </nav>
</header>

<section class="hero">
  <div class="hero-visual" role="img" aria-label="Photo of a businessman holding a glowing digital brain network in his hand"></div>
  <svg class="hero-arrow left" width="14" height="24" viewBox="0 0 14 24"><path d="M12 2 2 12l10 10" fill="none" stroke="#fff" stroke-width="3"/></svg>
  <svg class="hero-arrow right" width="14" height="24" viewBox="0 0 14 24"><path d="M2 2l10 10L2 22" fill="none" stroke="#fff" stroke-width="3"/></svg>
  <div class="hero-copy">
    <h1 class="hero-title">Plover, by <span>Varlomex</span></h1>
    <p class="hero-sub">The new standard in contact center customer experience</p>
    <span class="btn-more">Find out more</span>
  </div>
  <div class="cta-row">
    <div class="cta demo">
      <svg width="14" height="14" viewBox="0 0 14 14"><rect x="1" y="2" width="12" height="11" fill="none" stroke="#fff" stroke-width="1.5"/><path d="M1 5h12" stroke="#fff" stroke-width="1.5"/></svg>
      Request a demo
    </div>
    <div class="cta contact">
      <svg width="14" height="12" viewBox="0 0 14 12"><rect x="1" y="1" width="12" height="10" fill="none" stroke="#fff" stroke-width="1.5"/><path d="M1 1l6 5 6-5" fill="none" stroke="#fff" stroke-width="1.5"/></svg>
      Contact us
    </div>
  </div>
</section>

<section class="news">
  <h2 class="section-title">RECENT NEWS</h2>
  <div class="title-rule"></div>
  <div class="news-grid">
    <article class="news-card"><div class="news-image img-a" role="img" aria-label="Photo of a hand touching digital interface icons"></div><div class="news-body"><div class="news-meta">POSTED BY <span>ADMIN</span></div>New language models now power faster replies for large contact centres.</div></article>
    <article class="news-card"><div class="news-image img-b" role="img" aria-label="Photo of a finger tapping a tablet screen"></div><div class="news-body"><div class="news-meta">POSTED BY <span>ADMIN</span></div>Our team shares early results from a year of speech research.</div></article>
    <article class="news-card"><div class="news-image img-c" role="img" aria-label="Photo of glowing blue data network lights"></div><div class="news-body"><div class="news-meta">POSTED BY <span>ADMIN</span></div>How banks use language tools to answer customers around the clock.</div></article>
    <article class="news-card"><div class="news-image img-d" role="img" aria-label="Photo of people working together at a desk with laptops"></div><div class="news-body"><div class="news-meta">POSTED BY <span>ADMIN</span></div>Varlomex joins an industry forum on responsible use of machine learning.</div></article>
    <article class="news-card"><div class="news-image img-e" role="img" aria-label="Photo of a business meeting over a world map"></div><div class="news-body"><div class="news-meta">POSTED BY <span>ADMIN</span></div>Expanding across Asia with new partners and a fresh Chinese interface.</div></article>
    <article class="news-card"><div class="news-image img-f" role="img" aria-label="Photo of a robot hand meeting a human hand"></div><div class="news-body"><div class="news-meta">POSTED BY <span>ADMIN</span></div>Software makers can now bundle Plover Speech inside their own products.</div></article>
  </div>
  <div class="pager">
    <svg width="10" height="16" viewBox="0 0 10 16"><path d="M8 2 2 8l6 6" fill="none" stroke="#333" stroke-width="2"/></svg>
    <svg width="10" height="16" viewBox="0 0 10 16"><path d="M2 2l6 6-6 6" fill="none" stroke="#333" stroke-width="2"/></svg>
  </div>
</section>

<section class="stories">
  <h2 class="section-title">SUCCESS STORIES FROM OUR PARTNERS</h2>
  <div class="title-rule"></div>
  <div class="story-row">
    <div class="story"><div class="avatar" role="img" aria-label="Portrait photo of a partner"></div><p class="story-name">Daniel Hartwell, <span>Northbay Analytics</span></p><p class="story-text">Our support teams resolved requests faster after moving to the platform, and our customers noticed the difference within weeks. The rollout was smooth and the team was always available to help.</p></div>
    <div class="story"><div class="avatar" role="img" aria-label="Portrait photo of a partner"></div><p class="story-name">Daniel Hartwell, <span>Northbay Analytics</span></p><p class="story-text">Our support teams resolved requests faster after moving to the platform, and our customers noticed the difference within weeks. The rollout was smooth and the team was always available to help.</p></div>
    <div class="story"><div class="avatar" role="img" aria-label="Portrait photo of a partner"></div><p class="story-name">Daniel Hartwell, <span>Northbay Analytics</span></p><p class="story-text">Our support teams resolved requests faster after moving to the platform, and our customers noticed the difference within weeks. The rollout was smooth and the team was always available to help.</p></div>
  </div>
</section>

<footer class="site-footer">
  <div class="footer-main">
    <div class="footer-brand">VARLOMEX</div>
    <div class="footer-col"><h4>Artificial Intelligence</h4><p>What is AI</p><p>AI vs ML</p><p>The Future of AI</p></div>
    <div class="footer-col"><h4>About</h4><p>Company</p><p>Management</p><p>Careers</p></div>
    <div class="footer-col"><h4>Services</h4><p>Implementation Services</p><p>Business Consulting</p></div>
    <div class="footer-col"><h4>Partners</h4><p>Find a Partner</p><p>Become a Partner</p></div>
    <div class="footer-col"><h4>Products</h4><p>Plover - Text</p><p>Plover - Speech</p></div>
  </div>
  <div class="footer-bar">
    <span>© 2018 Varlomex | All Rights Reserved</span>
    <span class="legal">Sitemap | Privacy Policy | Terms Of Use
      <svg width="14" height="14" viewBox="0 0 14 14"><rect x="1" y="1" width="12" height="12" fill="none" stroke="#9a9a9a"/><path d="M4 9l3-3 3 3" fill="none" stroke="#9a9a9a" stroke-width="1.5"/></svg>
    </span>
  </div>
</footer>

</body>
</html>
```